Carpet cleaning company focused on high quality needs business cards

We are a growing company that just merged with another company and need to design a new business card. We do both residential as well as commercial cleaning. We do carpet, tile & grout, upholstery, hard floors, and stain & pet odor removal. We treat our customers like family and strive to achieve outstanding results with every job.

```html
<!DOCTYPE html>
<html lang="en">
<head>
<meta charset="utf-8">
<title>Hearthside Steam Cleaning – Business Cards</title>
<link href="https://fonts.googleapis.com/css2?family=Open+Sans:wght@400;600;700;800&display=swap" rel="stylesheet">
<style>
  :root {
    --stage: #232323;
    --paper: #ffffff;
    --ink: #111111;
    --brand-red: #ef4540;
    --brand-blue: #0282c3;
    --text-on-blue: #ffffff;
    --card-w: 560px;
    --card-h: 320px;
  }
  * { box-sizing: border-box; margin: 0; padding: 0; }
  html, body {
    width: 1200px; height: 780px; overflow: hidden;
    background: var(--stage);
    font-family: "Open Sans", Arial, sans-serif;
  }
  .stage {
    width: 1200px; height: 780px;
    display: flex; align-items: center; justify-content: center; gap: 40px;
  }
  .card {
    position: relative;
    width: var(--card-w); height: var(--card-h);
    background: var(--paper);
    border-radius: 22px;
    overflow: hidden;
    box-shadow: 0 14px 30px rgba(0,0,0,.55);
  }

  /* Brand lockup */
  .brand { display: flex; align-items: center; gap: 12px; }
  .brand-square { width: 56px; height: 56px; background: var(--brand-red); flex: none; }
  .brand-name {
    font-weight: 800; color: var(--ink); line-height: 1.05;
    text-transform: uppercase; letter-spacing: .5px;
  }

  /* Front card */
  .card-front { display: flex; flex-direction: column; align-items: center; padding-top: 62px; }
  .card-front .brand-square { width: 86px; height: 86px; }
  .card-front .brand-name { font-size: 30px; }
  .services { margin-top: 34px; width: 500px; text-align: center; }
  .services-heading {
    display: flex; align-items: center; gap: 10px;
    color: var(--brand-red); font-weight: 600; font-size: 13px; text-transform: uppercase;
  }
  .services-heading::before, .services-heading::after {
    content: ""; flex: 1; height: 1.5px; background: var(--brand-red);
  }
  .services-list { list-style: none; margin-top: 6px; font-size: 12px; color: var(--ink); line-height: 1.6; }
  .services-list li { display: inline; }
  .services-list li::before {
    content: ""; display: inline-block; width: 7px; height: 7px; border-radius: 50%;
    background: var(--brand-red); margin: 0 5px 1px 6px; vertical-align: middle;
  }
  .services-list .row { display: block; white-space: nowrap; }

  /* Back card */
  .card-back .wave { position: absolute; inset: 0; width: 100%; height: 100%; }
  .card-back .brand { position: absolute; top: 16px; right: 40px; }
  .card-back .brand-square { width: 42px; height: 42px; }
  .card-back .brand-name { font-size: 18px; }
  .contact {
    position: absolute; left: 42px; top: 160px; color: var(--text-on-blue);
  }
  .contact-name { font-size: 21px; font-weight: 700; line-height: 1.1; }
  .contact-title { font-size: 13px; font-weight: 600; margin-top: 2px; }
  .contact-address { font-size: 11.5px; margin-top: 8px; line-height: 1.4; }
  .contact-lines { list-style: none; margin-top: 6px; font-size: 11.5px; line-height: 1.45; }
  .contact-lines li { display: flex; align-items: center; gap: 8px; }
  .contact-lines svg { width: 12px; height: 12px; flex: none; fill: var(--text-on-blue); }
</style>
</head>
<body>
<main class="stage">

  <section class="card card-front" aria-label="Business card front">
    <div class="brand">
      <span class="brand-square" aria-hidden="true"></span>
      <span class="brand-name">Hearthside<br>Steam Cleaning</span>
    </div>
    <div class="services">
      <h2 class="services-heading">Our Services</h2>
      <ul class="services-list">
        <span class="row"><li>Both residential as well as commercial cleaning</li></span>
        <span class="row"><li>Carpet</li><li>Tile &amp; grout</li><li>Upholstery</li><li>Hard floors</li><li>Stain &amp; pet odor removal</li></span>
      </ul>
    </div>
  </section>

  <section class="card card-back" aria-label="Business card back">
    <svg class="wave" viewBox="0 0 560 320" preserveAspectRatio="none" aria-hidden="true">
      <path d="M0,145 C110,112 250,110 380,110 C470,110 530,96 560,82 L560,320 L0,320 Z" fill="var(--brand-blue)"/>
      <path d="M300,110 C400,112 500,100 560,68 L560,84 C505,108 410,116 300,110 Z" fill="var(--ink)"/>
      <path d="M50,128 C150,100 290,96 400,96 C480,96 530,80 556,56 L560,68 C530,90 470,104 400,104 C300,106 170,108 50,128 Z" fill="var(--brand-red)"/>
    </svg>
    <div class="brand">
      <span class="brand-square" aria-hidden="true"></span>
      <span class="brand-name">Hearthside<br>Steam Cleaning</span>
    </div>
    <div class="contact">
      <h1 class="contact-name">Marta Velinska</h1>
      <p class="contact-title">Managing Director</p>
      <p class="contact-address">418 Linden Ave. Suite 120<br>Oakdale, TX 75010</p>
      <ul class="contact-lines">
        <li><svg viewBox="0 0 24 24" aria-hidden="true"><path d="M6.6 10.8a15.1 15.1 0 0 0 6.6 6.6l2.2-2.2a1 1 0 0 1 1-.25 11.4 11.4 0 0 0 3.6.57 1 1 0 0 1 1 1V20a1 1 0 0 1-1 1A17 17 0 0 1 3 4a1 1 0 0 1 1-1h3.5a1 1 0 0 1 1 1c0 1.25.2 2.45.57 3.57a1 1 0 0 1-.25 1z"/></svg>(555) 210-4478</li>
        <li><svg viewBox="0 0 24 24" aria-hidden="true"><path d="M3 5h18v14H3zm2 2v.5l7 4.5 7-4.5V7zm0 2.8V17h14V9.8l-7 4.5z"/></svg>hello@hearthsidesteam.com</li>
        <li><svg viewBox="0 0 24 24" aria-hidden="true"><path d="M12 2a10 10 0 1 0 0 20 10 10 0 0 0 0-20zm6.9 9h-3a15 15 0 0 0-1.3-5.6A8 8 0 0 1 18.9 11zM12 4.1c.9 1.2 1.8 3.6 1.9 6.9h-3.8c.1-3.3 1-5.7 1.9-6.9zM9.4 5.4A15 15 0 0 0 8.1 11h-3a8 8 0 0 1 4.3-5.6zM5.1 13h3a15 15 0 0 0 1.3 5.6A8 8 0 0 1 5.1 13zm6.9 6.9c-.9-1.2-1.8-3.6-1.9-6.9h3.8c-.1 3.3-1 5.7-1.9 6.9zm2.6-1.3a15 15 0 0 0 1.3-5.6h3a8 8 0 0 1-4.3 5.6z"/></svg>www.hearthsidesteam.com</li>
      </ul>
    </div>
  </section>

</main>
</body>
</html>
```